International business needs business cards

Our company, DRV Ventures Inc. is in the business of supplying a range construction products with particular emphasis on CEMENT. We have developed our own brand - TORVAN SUPPLIES - with which to infiltrate the market. We are launching our brand of cement (TORVAN Type IS Cement) into the Caribbean which is unlike anything this market has ever seen. A monopoly has existed here for the past 60-odd years and the market has now opened to allow the importation of other brands and consumers are anxious and ready for change/improvement. We are very excited to be launching and want to make a great first impression. We will be conducting workshops and seminars (from government level to the hardware store owners) and we want our business card to give us the strong, confident introduction that we need.

Target Market(s)

construction; builders; engineers; home owners

Industry/Entity Type

Construction

Contact Information for Business Card

Marisol Depree
CEO
cell # 1 555 4180736
Ground floor,Lindell Plaza Suite 2734
George Town,Grand Cayman
Cayman Islands,KY1-4823
EMAIL: m.depree@drvventuresinc.example
web site drvventuresinc.example

COMPANY: skype info drv.ventures.example

second card
Yvette Brannock-Depree
CFO
CELL# 1 555 607 3941
George Town,Grand Cayman
Cayman Islands,KY1-4823
EMAIL: y.brannockdepree@drvventuresinc.example
website drvventuresinc.example

Requirements
Must have
• Business cards must display BOTH logos - DRV is the company and TORVAN is the brand.

```html
<!DOCTYPE html>
<html lang="en">
<head>
<meta charset="utf-8">
<title>DRV Ventures Inc. – Business Card</title>
<link rel="stylesheet" href="https://fonts.googleapis.com/css2?family=Arimo:wght@400;700&display=swap">
<style>
  :root {
    --page-bg: #e9e6e1;
    --card-black: #0c0c0c;
    --card-black-sheen: #2a2a2a;
    --card-white: #ffffff;
    --brand-red: #8e1a1d;
    --brand-red-dark: #6d1214;
    --ink: #111111;
    --ink-soft: #666666;
    --rule: #a3282b;
  }
  * { box-sizing: border-box; margin: 0; padding: 0; }
  html, body {
    width: 1200px; height: 950px; overflow: hidden;
    background: var(--page-bg);
    font-family: "Arimo", Arial, sans-serif;
  }
  .canvas {
    position: relative; width: 1200px; height: 950px;
  }
  .card {
    position: absolute; left: 230px;
    width: 740px; height: 423px;
    box-shadow: 0 10px 24px rgba(0,0,0,.25);
    overflow: hidden;
  }

  /* Back side */
  .card-back {
    top: 35px;
    background: linear-gradient(160deg, var(--card-black-sheen) 0%, var(--card-black) 45%, var(--card-black) 100%);
    color: #fff;
  }
  .back-logo {
    position: absolute; top: 130px; left: 0; width: 100%;
    display: flex; justify-content: center; align-items: center; gap: 18px;
  }
  .logo-square {
    width: 96px; height: 96px; background: var(--brand-red);
  }
  .back-logo .logo-name {
    font-weight: 700; font-size: 34px; color: #ffffff;
  }
  .back-web {
    position: absolute; top: 290px; width: 100%; text-align: center;
    font-size: 17px; letter-spacing: 4px; color: #e6e6e6;
  }

  /* Front side */
  .card-front {
    top: 492px;
    background: var(--card-white);
  }
  .front-logo {
    position: absolute; left: 48px; top: 118px;
    display: flex; align-items: center; gap: 12px;
  }
  .front-logo .logo-square { width: 64px; height: 64px; }
  .front-logo .logo-name {
    font-weight: 700; font-size: 30px; color: var(--ink);
  }
  .brand-mark {
    position: absolute; right: 56px; top: 26px;
    display: flex; flex-direction: column; align-items: center; gap: 10px;
  }
  .brand-crest {
    width: 120px; height: 90px;
    background: radial-gradient(circle, #9a9a9a 0%, #4a4a4a 100%);
    border-radius: 50% 50% 40% 40%;
  }
  .brand-name {
    font-weight: 700; font-size: 15px; letter-spacing: 1px; color: var(--ink);
  }
  .divider {
    position: absolute; left: 48px; right: 48px; top: 212px;
    height: 2px; background: var(--rule);
  }
  .person {
    position: absolute; left: 48px; top: 230px;
  }
  .person-name {
    font-size: 24px; color: var(--brand-red);
  }
  .person-title {
    font-size: 16px; color: var(--ink); margin-top: 4px;
    padding-bottom: 8px; border-bottom: 1px solid var(--rule); width: 230px;
  }
  .address {
    font-style: normal; font-size: 15px; line-height: 1.45;
    color: var(--ink-soft); margin-top: 8px;
  }
  .contact-list {
    position: absolute; right: 48px; top: 232px;
    list-style: none; font-size: 15px; color: var(--ink-soft);
  }
  .contact-list li {
    display: flex; justify-content: flex-end; align-items: center;
    gap: 10px; height: 26px;
  }
  .contact-icon { width: 16px; height: 16px; }
  .footer-band {
    position: absolute; left: 0; right: 0; bottom: 0; height: 34px;
    background: linear-gradient(180deg, var(--brand-red) 0%, var(--brand-red-dark) 100%);
    border-top: 4px solid #d9d9d9;
  }
</style>
</head>
<body>
<main class="canvas">

  <section class="card card-back" aria-label="Card back">
    <div class="back-logo">
      <div class="logo-square"></div>
      <span class="logo-name">DRV Ventures Inc.</span>
    </div>
    <p class="back-web">www.drvventuresinc.example</p>
  </section>

  <section class="card card-front" aria-label="Card front">
    <div class="front-logo">
      <div class="logo-square"></div>
      <span class="logo-name">DRV Ventures Inc.</span>
    </div>

    <div class="brand-mark">
      <div class="brand-crest" role="img" aria-label="TORVAN SUPPLIES brand crest emblem"></div>
      <span class="brand-name">TORVAN SUPPLIES</span>
    </div>

    <div class="divider"></div>

    <div class="person">
      <h1 class="person-name">Marisol Depree</h1>
      <p class="person-title">CEO</p>
      <address class="address">
        Ground floor<br>
        Lindell Plaza Suite 2734<br>
        George Town,Grand Cayman<br>
        Cayman Islands,KY1-4823
      </address>
    </div>

    <ul class="contact-list">
      <li>1 555 4180736
        <svg class="contact-icon" viewBox="0 0 16 16" aria-hidden="true">
          <rect x="4" y="1" width="8" height="14" rx="1.5" fill="none" stroke="#a3282b" stroke-width="1.6"/>
          <circle cx="8" cy="12.5" r="0.9" fill="#a3282b"/>
        </svg>
      </li>
      <li>m.depree@drvventuresinc.example
        <svg class="contact-icon" viewBox="0 0 16 16" aria-hidden="true">
          <rect x="1" y="3" width="14" height="10" rx="1" fill="#a3282b"/>
          <path d="M1.5 3.5 L8 9 L14.5 3.5" fill="none" stroke="#fff" stroke-width="1.2"/>
        </svg>
      </li>
      <li>drvventuresinc.example
        <svg class="contact-icon" viewBox="0 0 16 16" aria-hidden="true">
          <circle cx="8" cy="8" r="7" fill="#a3282b"/>
          <ellipse cx="8" cy="8" rx="3" ry="7" fill="none" stroke="#fff" stroke-width="1"/>
          <line x1="1" y1="8" x2="15" y2="8" stroke="#fff" stroke-width="1"/>
        </svg>
      </li>
    </ul>

    <div class="footer-band"></div>
  </section>

</main>
</body>
</html>
```